A website for a Maltese Law Firm

Our law firm needs a website to further its business. The site should have a simple yet effective design. We would need the following sections: About us, Practice Areas, About Malta, Contact. These should be further split as follows:

About us: Our firm, Our values, What others say, Offices

Practice Areas: Crimimal, Citizenship & Residence, Sovereign Patron Pathway, Criminal Defence, Civil Litigation, Arbitration and ADR, Commercial and Corporate, Media Law.

About Malta: just one section.

Contact: Just one section

We would also need a news feed at the front of the site to include latest news regarding our cases.

At the bottom we need a section for our Terms and a Privacy Statement.

Our logo is being attached.

Target Market(s)

All clients looking for legal assistance in Malta

Industry/Entity Type

Legal

Coding

Coded - Design and coding required

Number of Pages Required

1 page

Requirements
Must have
• It must be simple yet striking.

```html
<!DOCTYPE html>
<html lang="en">
<head>
<meta charset="utf-8">
<title>Mercieca &amp; Falzon Advocates</title>
<link href="https://fonts.googleapis.com/css2?family=Cinzel:wght@400;700&family=Open+Sans:wght@400;600;700&display=swap" rel="stylesheet">
<style>
:root{
  --ink:#1d1d1f;
  --dark:#151515;
  --darker:#0c0c0c;
  --text:#5a5a5a;
  --muted:#8a8a8a;
  --accent:#2f86c6;
  --accent-deep:#1a5e93;
  --light:#f2f2f2;
  --line:#d6d6d6;
  --white:#ffffff;
}
*{box-sizing:border-box;margin:0;padding:0}
html,body{width:1200px;height:3724px;overflow:hidden}
body{font-family:"Open Sans",Arial,sans-serif;color:var(--text);background:var(--white);font-size:15px;line-height:1.6}
.serif{font-family:"Cinzel",Georgia,serif}
ul{list-style:none}

/* header */
.site-header{position:relative;height:112px;background:var(--darker);color:var(--white)}
.top-social{position:absolute;left:80px;top:10px;display:flex;gap:10px}
.top-social span{width:18px;height:18px;border-radius:50%;background:#555}
.top-phone{position:absolute;right:80px;top:6px;display:flex;align-items:center;gap:8px;font-size:14px}
.brand{position:absolute;left:80px;top:42px;font-family:"Cinzel",Georgia,serif;font-size:30px;font-weight:700;color:var(--white);letter-spacing:1px}
.main-nav{position:absolute;right:80px;top:58px;display:flex;gap:34px;font-size:15px}
.main-nav a{color:#ddd;text-decoration:none;padding-bottom:6px}
.main-nav a.active{color:var(--white);border-bottom:2px solid var(--white)}

/* hero */
.hero{position:relative;height:572px;background:linear-gradient(135deg,#5a3a20 0%,#2a1c12 45%,#0f0c0a 100%)}
.hero-photo{position:absolute;inset:0}
.hero-title{position:absolute;left:80px;top:440px;font-family:"Cinzel",Georgia,serif;font-size:46px;line-height:1.2;color:var(--white);font-weight:700}
.slider-arrow{position:absolute;top:290px;width:36px;height:48px;background:rgba(0,0,0,.6);display:flex;align-items:center;justify-content:center}
.slider-arrow.prev{left:0}.slider-arrow.next{right:0}

/* section headings */
.section-title{text-align:center;font-family:"Cinzel",Georgia,serif;font-size:46px;color:#3a3a3a;letter-spacing:1px}
.section-rule{width:320px;height:1px;background:var(--line);margin:10px auto 0}

/* about */
.about{height:516px;padding:44px 200px 0}
.about p{text-align:center;font-size:15px;margin-top:24px}
.about-features{display:flex;gap:60px;justify-content:center;margin-top:54px}
.feature{display:flex;gap:18px;width:400px}
.feature-icon{width:92px;height:92px;border:1px solid var(--line);flex:none;display:flex;align-items:center;justify-content:center}
.feature h3{font-family:"Cinzel",Georgia,serif;font-size:17px;color:var(--ink)}
.feature p{text-align:left;margin:0;font-size:12px;line-height:1.5}

/* practice areas */
.practice{height:1320px;background:var(--light);padding-top:40px}
.practice-grid{display:grid;grid-template-columns:repeat(3,328px);grid-auto-rows:356px;gap:24px 26px;justify-content:center;margin-top:50px}
.area{position:relative;overflow:hidden}
.area-photo{position:absolute;inset:0}
.area-name{position:absolute;left:0;right:0;bottom:40px;text-align:center;font-family:"Cinzel",Georgia,serif;font-size:27px;line-height:1.1;color:var(--white);text-shadow:0 2px 4px rgba(0,0,0,.6)}
.area.is-open .area-overlay{position:absolute;inset:0;background:rgba(38,120,185,.72);color:var(--white);text-align:center;padding:150px 24px 0}
.area.is-open .area-name{position:static;margin-bottom:12px}
.area-overlay p{font-size:14px;line-height:1.4}
.area-overlay .more{width:34px;height:34px;border-radius:50%;border:2px solid var(--white);margin:18px auto 0}

/* case studies */
.cases{height:520px;background:linear-gradient(180deg,#1a1612 0%,#0f0d0b 100%);padding-top:38px;color:#bbb}
.cases .section-title{color:var(--white)}
.cases .section-rule{background:#555}
.case-grid{display:flex;gap:26px;justify-content:center;margin-top:36px}
.case{width:328px}
.case-photo{position:relative;height:152px}
.case-date{position:absolute;left:0;top:0;background:var(--white);color:var(--ink);width:44px;text-align:center;font-size:18px;font-weight:700;line-height:1.1;padding:4px 0}
.case-date small{display:block;font-size:11px;font-weight:400;background:var(--accent);color:var(--white)}
.case h4{color:var(--accent);font-size:15px;margin-top:12px}
.case p{font-size:12px;line-height:1.5;margin-top:4px}
.case .read{font-size:12px;color:var(--white);margin-top:6px}
.view-all{display:flex;justify-content:center;gap:4px;margin-top:14px}
.view-all span{background:#333;color:var(--white);font-size:12px;padding:5px 16px}
.view-all b{background:#444;width:28px;display:flex;align-items:center;justify-content:center}

/* testimonials */
.testimonials{position:relative;height:360px;padding-top:44px}
.testimonial-row{display:flex;gap:80px;justify-content:center;margin-top:40px}
.testimonial{display:flex;gap:30px;width:440px}
.avatar-col{text-align:center;flex:none;width:100px}
.avatar{width:96px;height:96px;border-radius:50%;background:linear-gradient(135deg,#c9d2db,#8a97a5)}
.avatar-col span{display:block;font-size:13px;margin-top:14px;color:var(--ink)}
.testimonial p{font-size:14px;line-height:1.6}
.t-arrow{position:absolute;top:206px;width:30px;height:30px;border-radius:50%;border:1px solid var(--line);display:flex;align-items:center;justify-content:center}
.t-arrow.prev{left:30px}.t-arrow.next{right:30px}

/* footer */
.site-footer{position:relative;height:290px;background:var(--dark);color:#bbb;font-size:13px}
.footer-col{position:absolute;top:40px}
.footer-col h5{color:var(--accent);font-size:15px;text-transform:uppercase;font-weight:600;margin-bottom:14px}
.quick-links li{margin-bottom:6px;color:#ddd}
.quick-links li::before{content:"› ";color:var(--accent)}
.contact-list li{display:flex;gap:10px;margin-bottom:8px;align-items:flex-start}
.contact-list svg{flex:none;margin-top:3px}
.map{position:absolute;left:520px;top:96px;width:240px;height:120px;background:linear-gradient(135deg,#e8e6df,#cfd8c8)}
.footer-brand{position:absolute;right:80px;top:18px;font-family:"Cinzel",Georgia,serif;font-size:26px;font-weight:700;color:var(--white)}
.footer-social{position:absolute;right:130px;top:70px;display:flex;gap:10px}
.footer-social span{width:30px;height:30px;border-radius:50%;background:var(--accent-deep)}
.footer-legal{position:absolute;right:80px;top:240px;font-size:12px;color:#888}
.bottom-bar{height:34px;background:#080808;text-align:center;color:#777;font-size:12px;line-height:34px}
</style>
</head>
<body>

<header class="site-header">
  <div class="top-social"><span></span><span></span><span></span><span></span></div>
  <div class="top-phone">
    <svg width="14" height="14" viewBox="0 0 24 24"><path fill="#fff" d="M6.6 10.8a15 15 0 0 0 6.6 6.6l2.2-2.2c.3-.3.7-.4 1-.2 1.1.4 2.3.6 3.6.6.6 0 1 .4 1 1V20c0 .6-.4 1-1 1A17 17 0 0 1 3 4c0-.6.4-1 1-1h3.5c.6 0 1 .4 1 1 0 1.3.2 2.5.6 3.6.1.3 0 .7-.2 1z"/></svg>
    555-010-2040
  </div>
  <div class="brand">Mercieca &amp; Falzon</div>
  <nav class="main-nav">
    <a class="active" href="#">Home</a><a href="#">About Us</a><a href="#">Practice Areas</a><a href="#">Case Studies</a><a href="#">Contact Us</a>
  </nav>
</header>

<section class="hero">
  <div class="hero-photo" role="img" aria-label="Scales of justice, a judge's gavel and stacked law books on a desk"></div>
  <h1 class="hero-title">Realize Your Constitutional<br>Right For Qualified Legal Help</h1>
  <div class="slider-arrow prev"><svg width="12" height="18"><path d="M10 2 3 9l7 7" stroke="#fff" stroke-width="2" fill="none"/></svg></div>
  <div class="slider-arrow next"><svg width="12" height="18"><path d="m2 2 7 7-7 7" stroke="#fff" stroke-width="2" fill="none"/></svg></div>
</section>

<section class="about">
  <h2 class="section-title">About Mercieca &amp; Falzon</h2>
  <div class="section-rule"></div>
  <p>Lorem ipsum dolor sit amet, consectetuer adipiscing elit, sed diam nonummy nibh euismod tincidunt ut laoreet dolore magna aliquam erat volutpat. Ut wisi enim ad minim veniam, quis nostrud exerci tation ullamcorper suscipit lobortis nisl ut aliquip ex ea commodo consequat. Duis autem vel eum iriure dolor in hendrerit in vulputate velit esse molestie consequat.</p>
  <p>Lorem ipsum dolor sit amet, consectetuer adipiscing elit, sed diam nonummy nibh euismod tincidunt ut laoreet dolore magna aliquam erat volutpat. Ut wisi enim ad minim veniam, quis nostrud exerci tation ullamcorper suscipit lobortis nisl ut aliquip ex ea commodo consequat. Duis autem vel eum iriure dolor in hendrerit in vulputate velit esse molestie consequat.</p>
  <div class="about-features">
    <div class="feature">
      <div class="feature-icon"><svg width="44" height="34" viewBox="0 0 44 34"><path d="M2 14 12 4l8 6 6-4 16 10-10 12-10-6-6 6L2 18z" fill="none" stroke="#555" stroke-width="2"/></svg></div>
      <div><h3>Our Values</h3><p>Integrity, discretion and careful advice guide every matter we take on for our clients here.</p></div>
    </div>
    <div class="feature">
      <div class="feature-icon"><svg width="40" height="40" viewBox="0 0 40 40"><path d="M4 14 20 4l16 10zM8 16v16M16 16v16M24 16v16M32 16v16M4 34h32" fill="none" stroke="#555" stroke-width="2"/></svg></div>
      <div><h3>Our Firm</h3><p>A team of advocates serving private and corporate clients across Malta and abroad.</p></div>
    </div>
  </div>
</section>

<section class="practice">
  <h2 class="section-title">Practice Areas</h2>
  <div class="section-rule"></div>
  <div class="practice-grid">
    <div class="area is-open">
      <div class="area-photo" role="img" aria-label="Hands in handcuffs" style="background:linear-gradient(160deg,#6a8fb0,#2d4a66)"></div>
      <div class="area-overlay">
        <div class="area-name">Criminal</div>
        <p>Lorem ipsum dolor sit amet, consectetuer adipiscing elit sed diam nonummy nibh.</p>
        <div class="more"></div>
      </div>
    </div>
    <div class="area"><div class="area-photo" role="img" aria-label="A family in front of a house" style="background:linear-gradient(180deg,#a9c4de,#6f7f6a)"></div><div class="area-name">Citizenship &amp;<br>Residence</div></div>
    <div class="area"><div class="area-photo" role="img" aria-label="A couple meeting an adviser" style="background:linear-gradient(160deg,#d9d2c6,#8a7a66)"></div><div class="area-name">Sovereign Patron<br>Pathway</div></div>
    <div class="area"><div class="area-photo" role="img" aria-label="A gavel on a desk" style="background:linear-gradient(160deg,#7a3a1f,#1f1410)"></div><div class="area-name">Criminal Defence</div></div>
    <div class="area"><div class="area-photo" role="img" aria-label="A yellow hard hat" style="background:linear-gradient(160deg,#e8c23a,#8a6a14)"></div><div class="area-name">Civil Litigation</div></div>
    <div class="area"><div class="area-photo" role="img" aria-label="Press microphones" style="background:linear-gradient(160deg,#dcdcdc,#6a6a6a)"></div><div class="area-name">Media Law</div></div>
    <div class="area"><div class="area-photo" role="img" aria-label="Two business people shaking hands" style="background:linear-gradient(160deg,#9a9a9a,#3a3a3a)"></div><div class="area-name">Arbitration<br>and ADR</div></div>
    <div class="area"><div class="area-photo" role="img" aria-label="A hand signing a contract" style="background:linear-gradient(160deg,#3a6fb0,#122a4a)"></div><div class="area-name">Commercial and<br>Corporate</div></div>
    <div class="area"><div class="area-photo" role="img" aria-label="Hands in handcuffs" style="background:linear-gradient(160deg,#8a8a8a,#2a2a2a)"></div><div class="area-name">Criminal</div></div>
  </div>
</section>

<section class="cases">
  <h2 class="section-title">Case Studies</h2>
  <div class="section-rule"></div>
  <div class="case-grid">
    <article class="case">
      <div class="case-photo" role="img" aria-label="Shelves of law books" style="background:linear-gradient(160deg,#a8722a,#4a2a10)"><div class="case-date">06<small>Jun</small></div></div>
      <h4>Appeal Won In Commercial Dispute</h4>
      <p>Our team secured a favourable ruling for a local trading company in a long running contract claim.</p>
      <div class="read">Read More ›</div>
    </article>
    <article class="case">
      <div class="case-photo" role="img" aria-label="Hands in handcuffs" style="background:linear-gradient(160deg,#6a6a6a,#2a2a2a)"><div class="case-date">06<small>Jun</small></div></div>
      <h4>Acquittal Secured In Fraud Trial</h4>
      <p>After a three week hearing the court cleared our client of all charges brought against him.</p>
      <div class="read">Read More ›</div>
    </article>
    <article class="case">
      <div class="case-photo" role="img" aria-label="A pen signing a document" style="background:linear-gradient(160deg,#e4e4e4,#8a8a8a)"><div class="case-date">07<small>Jun</small></div></div>
      <h4>Residence Granted To Investor Family</h4>
      <p>We guided a family through every step of their residence application from filing to approval.</p>
      <div class="read">Read More ›</div>
    </article>
  </div>
  <div class="view-all"><span>VIEW ALL</span><b><svg width="8" height="12"><path d="m1 1 5 5-5 5" stroke="#fff" stroke-width="2" fill="none"/></svg></b></div>
</section>

<section class="testimonials">
  <h2 class="section-title">Client Testimonials</h2>
  <div class="section-rule"></div>
  <div class="t-arrow prev"><svg width="8" height="12"><path d="M7 1 2 6l5 5" stroke="#999" stroke-width="2" fill="none"/></svg></div>
  <div class="t-arrow next"><svg width="8" height="12"><path d="m1 1 5 5-5 5" stroke="#999" stroke-width="2" fill="none"/></svg></div>
  <div class="testimonial-row">
    <div class="testimonial">
      <div class="avatar-col"><div class="avatar" role="img" aria-label="Client portrait"></div><span>– Mark Vella</span></div>
      <p>“ Clear advice from the very first meeting. The team explained every option and handled my case with great care and patience. I would gladly recommend them to anyone needing help. ”</p>
    </div>
    <div class="testimonial">
      <div class="avatar-col"><div class="avatar" role="img" aria-label="Client portrait"></div><span>– Clara Bonnici</span></div>
      <p>“ Professional, responsive and honest. They made a stressful process simple and kept me informed at every stage until the matter was fully resolved. ”</p>
    </div>
  </div>
</section>

<footer class="site-footer">
  <div class="footer-col" style="left:80px">
    <h5>Quick Links</h5>
    <ul class="quick-links"><li>Home</li><li>About Malta</li><li>Practice Areas</li><li>Case Studies</li><li>Contact Us</li></ul>
  </div>
  <div class="footer-col" style="left:300px">
    <h5>Contact Details</h5>
    <ul class="contact-list">
      <li><svg width="12" height="14" viewBox="0 0 12 16"><path d="M6 0a6 6 0 0 0-6 6c0 4 6 10 6 10s6-6 6-10a6 6 0 0 0-6-6zm0 8a2 2 0 1 1 0-4 2 2 0 0 1 0 4z" fill="#2f86c6"/></svg><span>Mercieca &amp; Falzon Advocates<br>14 Harbour Lane, Floor 2<br>Valletta VLT 0000, Malta</span></li>
      <li><svg width="12" height="12" viewBox="0 0 24 24"><path fill="#2f86c6" d="M6.6 10.8a15 15 0 0 0 6.6 6.6l2.2-2.2c.3-.3.7-.4 1-.2 1.1.4 2.3.6 3.6.6.6 0 1 .4 1 1V20c0 .6-.4 1-1 1A17 17 0 0 1 3 4c0-.6.4-1 1-1h3.5c.6 0 1 .4 1 1 0 1.3.2 2.5.6 3.6.1.3 0 .7-.2 1z"/></svg><span>555-010-2040</span></li>
      <li><svg width="12" height="12" viewBox="0 0 24 24"><path fill="#2f86c6" d="M4 4h16v16H4zM8 2v4M16 2v4" /></svg><span>555-010-2041</span></li>
      <li><svg width="12" height="10" viewBox="0 0 24 18"><path d="M1 1h22v16H1zM1 1l11 9 11-9" fill="none" stroke="#2f86c6" stroke-width="2"/></svg><span>hello@merciecafalzon.example</span></li>
    </ul>
  </div>
  <div class="map" role="img" aria-label="Street map of the office location"></div>
  <div class="footer-brand">Mercieca &amp; Falzon</div>
  <div class="footer-social"><span></span><span></span><span></span><span></span></div>
  <div class="footer-legal">Terms &amp; Conditions &nbsp;|&nbsp; Privacy Statement</div>
</footer>
<div class="bottom-bar">Copyright © 2024 Mercieca &amp; Falzon Advocates. All Rights Reserved.</div>

</body>
</html>
```